Web Design Project

Brightfold Publishing owns and operates a large number of editorial websites. These websites provides mostly consumers in the financial services space with information and price comparisons for a particular service.

Brightfold Publishing, as the holding company for each of these sites, currently has no website. We need to build a website targeted towards potential partners for our websites. The idea being that when we start a conversation with a partner, they can view our site and obtain some basic information about who we are.

The structure of the site is to be very simple, containing only a brief description about who we are, our contact details and a list of some of our websites:
• CoverVault.net.au
• MotorPolicyCheck.com.au
• DwellingCoverCheck.com.au
• MedicalCoverCheck.com.au
• LegacyCoverCheck.com.au
• JourneyCoverCheck.com.au
• AnimalCoverCheck.com.au
• PrivateLendingCheck.com.au
• MobileCoolingUnit.com.au
• FixedSavingsYield.com.au
• ThriftyHousehold.com.au
• CoinNana.com.au
• TameYourPlastic.com.au
• PurseMinder.com.au
• ThirdPartyClaimsCoverNational.com.au
• Trade-Cover.com.au
• MotorPolicyProviders.com.au
• MedicalCoverProviders.com.au
• DwellingCoverHub.com
• LegacyCoverHub.com
• EarningsShieldCoverHub.com
• MedicalCoverHub.com
• AnimalCoverHub.com
• PrivateLendingHub.com
• ChargePlasticHub.com
• DwellingLendingHub.com
• RetireNestEgg.net.au

The design of the site should say 'Internet company', 'professional', 'fresh thinking'. The design should not look like a corporate site that you would see from any corporate services business with images of people in suits. We are ultimately an Internet business and there should be a unique feel to the site.

We are open to a suggestion of a colour pallet as the holding company does not have an established logo.

Some sites that we like are:

http://www.quillmarsh-studio.co.uk/#home
http://previewbox00.layoutdock.example/wt_52418/index.html
http://previewbox00.layoutdock.example/wordpress_61942/
http://ponderloop.example/
http://www.brindlux.example/
http://www.tobiasvrankel.example/
http://www.slickfrontdoors.example/Corporate/design-ideas-detail.html?id=4197
http://pairmint.example/
http://orvendal.example/

Reason: Hi all, Apologies, but I need to extend the timeline. One of our key stakeholders is away for the next week. There are a few good designs that we have received to date and there are some tweaks that we would like to see before making a final decision. Thank you to everyone that has submitted designs - Have a great new year. Derek

Reason: Sorry to have to delay the deadline on this, but we did not find anything in the designs really resonated with us. We will have a further think about the existing designs that have been submitted and how we can provide more specific feedback to the designers to make some modifications to the designs.

Target Market(s)

We are targeting insurance companies / brokers that we are talking to. The idea is that we show a professional face to them.

Industry/Entity Type

Financial

Requirements
Must have
• Home Page (possibly integrated with About us details)
Contact Us
Our Sites

```html
<!DOCTYPE html>
<html lang="en">
<head>
<meta charset="utf-8">
<title>Brightfold Publishing</title>
<link href="https://fonts.googleapis.com/css2?family=Oswald:wght@500;700&family=Signika:wght@600&family=Open+Sans:wght@300;400;600&display=swap" rel="stylesheet">
<style>
:root{
  --teal:#1f6b67;
  --teal-deep:#15514e;
  --teal-light:#23726e;
  --teal-line:#3e8a85;
  --ink:#1b1b1b;
  --header-top:#fafafa;
  --header-bottom:#dcdcdc;
  --nav-text:#3a3a3a;
  --white:#ffffff;
  --accent:#e4f06a;
  --field-border:#4c9893;
  --field-text:#d9ece9;
  --footer-text:#6d6d6d;
  --placeholder:#dde3df;
}
*{box-sizing:border-box;margin:0;padding:0}
html,body{width:1100px;height:1200px;overflow:hidden}
body{position:relative;background:var(--teal-light);font-family:Arial,Helvetica,sans-serif;color:var(--white)}
.abs{position:absolute}

/* header */
.site-header{left:0;top:0;width:1100px;height:110px;background:linear-gradient(var(--header-top),var(--header-bottom))}
.brand{left:100px;top:26px;font-family:"Oswald",sans-serif;font-weight:700;font-size:36px;line-height:48px;color:var(--teal);letter-spacing:.5px}
.main-nav{left:581px;top:0;height:104px;display:flex}
.nav-item{position:relative;width:110px;height:104px;border-left:1px solid #cfcfcf;border-right:1px solid #fff;text-align:center;font-family:"Oswald",sans-serif;font-weight:500;font-size:18px;color:var(--nav-text);letter-spacing:.5px}
.nav-item svg{position:absolute;left:44px;top:10px}
.nav-item span{position:absolute;left:0;right:0;top:34px}
.nav-item.current{color:var(--white)}
.nav-tab{position:absolute;left:0;top:0}

/* bands */
.edge{left:0;width:1100px;height:12px;background:repeating-linear-gradient(90deg,#0c2a28 0 3px,#123836 3px 6px)}
.projects-band{left:0;top:120px;width:1100px;height:240px;background:var(--teal);border-bottom:1px solid var(--teal-line)}
.section-title{font-family:"Oswald",sans-serif;font-weight:700;font-size:17px;letter-spacing:0;text-transform:uppercase}
.rule{height:1px;background:var(--teal-line);border-bottom:1px solid var(--teal-deep)}
.slider-arrows{left:969px;top:151px;display:flex;gap:4px}
.project{width:177px;top:210px;height:134px;background:var(--teal-deep);border:1px solid var(--teal-line)}
.project .shot{position:absolute;left:7px;top:6px;width:162px;height:92px}
.project .name{position:absolute;left:0;right:0;top:115px;text-align:center;font-size:11px;color:var(--white)}

/* clients */
.client-frame{left:135px;top:454px;width:333px;height:254px;background:var(--white);box-shadow:0 10px 12px rgba(0,0,0,.35);padding:8px}
.client-shot{width:317px;height:226px;background:var(--placeholder)}
.perks{left:490px;top:466px;list-style:none;font-family:"Signika",sans-serif;font-weight:600;font-size:19px;line-height:30px;letter-spacing:.4px}
.perks li{display:flex;align-items:center;gap:12px}
.client-copy{left:494px;top:566px;width:452px;font-size:12.5px;line-height:20px;text-align:justify;hyphens:auto}

/* welcome + quote */
.divider{left:617px;top:744px;width:1px;height:362px;background:var(--teal-line)}
.welcome-copy{left:80px;top:814px;width:474px;font-size:12.5px;line-height:18px;text-align:justify}
.welcome-copy p+p{margin-top:18px;text-align:left}
.phone{left:80px;top:948px;width:436px;text-align:center;font-family:"Open Sans",sans-serif;font-weight:300;font-size:33px;color:var(--accent)}
.email-label{left:80px;top:994px;width:436px;text-align:center;font-size:13px}
.email{left:80px;top:1020px;width:436px;text-align:center;font-family:"Open Sans",sans-serif;font-weight:600;font-size:13px;color:var(--accent);letter-spacing:.3px}
.btn{height:43px;width:120px;background:linear-gradient(#2c2c2c,#0f0f0f);border-radius:4px;box-shadow:0 1px 0 var(--teal-line);display:flex;align-items:center;justify-content:center;gap:10px;font-family:"Oswald",sans-serif;font-weight:500;font-size:16px;color:var(--white);letter-spacing:0}
.field{left:688px;width:258px;height:37px;border:1px solid var(--field-border);border-radius:18px;background:rgba(255,255,255,.03);padding:0 16px;font-size:12.5px;line-height:35px;color:var(--field-text)}
.field.message{left:691px;top:953px;width:255px;height:100px;line-height:40px}

/* footer */
.site-footer{left:0;top:1128px;width:1100px;height:72px;background:linear-gradient(#fdfdfd,#e5e5e5)}
.footer-links{left:68px;top:0;display:flex;height:72px}
.footer-links a{width:161px;display:flex;align-items:center;justify-content:center;text-decoration:none;color:var(--footer-text);font-size:12.5px;border-right:1px solid #d6d6d6;margin-top:16px;height:38px}
.footer-links a:first-child{width:137px}
.footer-links a:last-child{border-right:0}
.copyright{right:62px;top:1155px;font-size:12.5px;color:var(--footer-text)}
</style>
</head>
<body>

<header class="site-header abs">
  <div class="brand abs">Brightfold Publishing</div>
  <nav class="main-nav abs">
    <div class="nav-item current">
      <svg class="nav-tab" width="110" height="96" viewBox="0 0 110 96" style="left:0;top:0"><path d="M2 0H108C96 30 90 92 54 95C20 92 20 40 2 0Z" fill="#1f6b67"/></svg>
      <svg width="20" height="20" viewBox="0 0 20 20"><path d="M10 2L1 10h3v8h4v-5h4v5h4v-8h3z" fill="#ffffff"/></svg>
      <span>Home</span>
    </div>
    <div class="nav-item">
      <svg width="20" height="20" viewBox="0 0 20 20"><circle cx="10" cy="6" r="4" fill="#9a9a9a"/><path d="M3 19c0-6 3-8 7-8s7 2 7 8z" fill="#9a9a9a"/></svg>
      <span>About</span>
    </div>
    <div class="nav-item">
      <svg width="22" height="22" viewBox="0 0 22 22"><circle cx="11" cy="11" r="9" fill="none" stroke="#3c7fb0" stroke-width="3" stroke-dasharray="3 2"/><circle cx="11" cy="11" r="4" fill="#3c7fb0"/></svg>
      <span>Projects</span>
    </div>
    <div class="nav-item">
      <svg width="22" height="22" viewBox="0 0 22 22"><rect x="1" y="1" width="20" height="20" rx="3" fill="#ececec" stroke="#8d8d8d"/><path d="M8 6h4v10H8" fill="none" stroke="#333" stroke-width="2"/></svg>
      <span>Contact</span>
    </div>
  </nav>
</header>

<div class="edge abs" style="top:108px"></div>

<section class="projects-band abs">
  <h2 class="section-title abs" style="left:84px;top:30px">Latest Projects</h2>
  <div class="slider-arrows abs" style="top:31px">
    <svg width="20" height="20" viewBox="0 0 20 20"><circle cx="10" cy="10" r="9" fill="none" stroke="#fff" stroke-width="1.6"/><path d="M12 5l-5 5 5 5" fill="none" stroke="#fff" stroke-width="2"/></svg>
    <svg width="20" height="20" viewBox="0 0 20 20"><circle cx="10" cy="10" r="9" fill="none" stroke="#fff" stroke-width="1.6"/><path d="M8 5l5 5-5 5" fill="none" stroke="#fff" stroke-width="2"/></svg>
  </div>
</section>

<div class="project abs" style="left:82px"><div class="shot" role="img" aria-label="Homepage screenshot of CoverVault.net.au" style="background:linear-gradient(#ffffff 0 30%,#eef1e8 30% 80%,#c8d9a8)"></div><div class="name">CoverVault.net.au</div></div>
<div class="project abs" style="left:273px"><div class="shot" role="img" aria-label="Homepage screenshot of ThriftyHousehold.com.au" style="background:linear-gradient(#2e2e2e 0 18%,#f4f4f4 18%)"></div><div class="name">ThriftyHousehold.com.au</div></div>
<div class="project abs" style="left:464px"><div class="shot" role="img" aria-label="Homepage screenshot of Trade-Cover.com.au" style="background:linear-gradient(#ffffff 0 25%,#e9e9e9 25% 45%,#fafafa 45%)"></div><div class="name">Trade-Cover.com.au</div></div>
<div class="project abs" style="left:655px"><div class="shot" role="img" aria-label="Homepage screenshot of LegacyCoverCheck.com.au" style="background:linear-gradient(#111 0 20%,#e8e8e8 20% 85%,#3c8a2a 85%)"></div><div class="name">LegacyCoverCheck.com.au</div></div>
<div class="project abs" style="left:846px"><div class="shot" role="img" aria-label="Homepage screenshot of JourneyCoverCheck.com.au" style="background:linear-gradient(90deg,#c23c8a 0 4%,transparent 4% 96%,#c23c8a 96%),linear-gradient(#111 0 25%,#e8e8e8 25%)"></div><div class="name">journeycovercheck.com.au</div></div>

<h2 class="section-title abs" style="left:84px;top:392px">Our Prestigious Clients</h2>
<div class="rule abs" style="left:82px;top:426px;width:940px"></div>

<svg class="abs" style="left:86px;top:540px" width="30" height="44" viewBox="0 0 30 44"><path d="M26 2L6 22l20 20" fill="none" stroke="#185653" stroke-width="7"/></svg>
<svg class="abs" style="left:986px;top:540px" width="30" height="44" viewBox="0 0 30 44"><path d="M4 2l20 20L4 42" fill="none" stroke="#185653" stroke-width="7"/></svg>

<div class="client-frame abs">
  <div class="client-shot" role="img" aria-label="Screenshot of a client car insurance comparison website"></div>
</div>

<ul class="perks abs">
  <li><svg width="20" height="18" viewBox="0 0 20 18"><path d="M2 10l5 5L18 2" fill="none" stroke="#fff" stroke-width="3.5"/></svg>No Strings Attached, Totally Free Quotes</li>
  <li><svg width="20" height="18" viewBox="0 0 20 18"><path d="M2 10l5 5L18 2" fill="none" stroke="#fff" stroke-width="3.5"/></svg>Great Australian Insurance Companies</li>
  <li><svg width="20" height="18" viewBox="0 0 20 18"><path d="M2 10l5 5L18 2" fill="none" stroke="#fff" stroke-width="3.5"/></svg>Start Saving Today</li>
</ul>
<p class="client-copy abs" lang="en">There's a wide range of car insurance options in Australia, which is impressive for a country of our size. It's easy to become overwhelmed given the number of com&shy;panies offering "the best", "the cheapest" or "the best and cheapest" car insur&shy;ance, but there are a few things you need to consider before you commit to one particular insurer.</p>

<h2 class="section-title abs" style="left:84px;top:753px">Welcome Message</h2>
<div class="rule abs" style="left:82px;top:790px;width:470px"></div>
<div class="divider abs"></div>

<div class="welcome-copy abs">
  <p>Brightfold Publishing is an Australian-based internet marketing company. We specialise in attracting customers from our directory of more than 100 sites to our network of trusted partners. Our skill lies in generating targeted traffic to our range of websites and identifying the right partners for each of the sites, ensuring that the visitors to our sites get what they are looking for.</p>
  <p>If you are interested in partnering with us on one or multiple of our sites, please contact us at :</p>
</div>
<div class="phone abs">02 8147 6630</div>
<div class="email-label abs">Or Email us @</div>
<div class="email abs">info@brightfoldpublishing.com.au</div>

<a class="btn abs" style="left:431px;top:1062px">READ MORE <svg width="20" height="20" viewBox="0 0 20 20"><circle cx="10" cy="10" r="10" fill="#fff"/><path d="M8 5l5 5-5 5" fill="none" stroke="#111" stroke-width="2.2"/></svg></a>

<h2 class="section-title abs" style="left:683px;top:753px">Request a Quote</h2>
<div class="rule abs" style="left:675px;top:790px;width:300px"></div>
<div class="field abs" style="top:810px">---- Name -----</div>
<div class="field abs" style="top:857px">---- Email -----</div>
<div class="field abs" style="top:905px">---- Phone -----</div>
<div class="field message abs">---- Your requirement details -----</div>
<a class="btn abs" style="left:822px;top:1062px">SUBMIT <svg width="20" height="20" viewBox="0 0 20 20"><circle cx="10" cy="10" r="10" fill="#fff"/><path d="M8 5l5 5-5 5" fill="none" stroke="#111" stroke-width="2.2"/></svg></a>

<div class="edge abs" style="top:1117px"></div>
<footer class="site-footer abs">
  <nav class="footer-links abs">
    <a>HOME</a><a>ABOUT</a><a>PROJECTS</a><a>CONTACT</a>
  </nav>
</footer>
<div class="copyright abs">Copyright Brightfold Publishing © 2011-12.</div>

</body>
</html>
```